Electrician Business Card/ company logo/small business

New Business Cards and logo needed that will catch peoples eye and say we went that extra step. Attached is a design possibly to be incorporated, if u have your own great, lets see it!... This will be a small local business. thank you for all you do!
Halvern Electric
Ned Fosky Owner
Journeyman Electrician
phone 1.555.208.3471
email: KQLHalvernElectric@quellmail.net
call for free estimate!
Updates

Accepted and approved for cards

Target Market(s)

support small local business

Industry/Entity Type

Electrical,

Contact Information for Business Card

name, title,company/ logo, phone, email, free estimate

Other font styles liked:
• easy to read

Colors

Designer to choose colors to be used in the design.

Requirements
Must have
• eye catching everything! logo and halvern electric listed on business card/logo, incorp logo in the background of card
Nice to have
• lightening bolts in eyes or around the triangle? vertical, modern, any design that would be unique and stand out
Should not have
• pinks, reds, yellows,brown

```html
<!DOCTYPE html>
<html lang="en">
<head>
<meta charset="utf-8">
<title>Halvern Electric – Business Card</title>
<link rel="stylesheet" href="https://fonts.googleapis.com/css2?family=Michroma&family=Roboto:wght@500&family=Open+Sans:wght@600&display=swap">
<style>
  :root {
    --backdrop: #6d8fc0;
    --card: #222324;
    --facet: rgba(255,255,255,0.035);
    --orange: #f08c1e;
    --red: #d9262b;
    --white: #ffffff;
    --grey-text: #e4e4e4;
    --rule: #3a3a3a;
  }
  * { margin: 0; padding: 0; box-sizing: border-box; }
  html, body { width: 1200px; height: 1200px; overflow: hidden; }
  body { background: var(--backdrop); position: relative; }

  .business-card {
    position: absolute; left: 276px; top: 60px;
    width: 648px; height: 1080px;
    background: var(--card);
    overflow: hidden;
  }
  .card-facets { position: absolute; inset: 0; }

  .brand {
    position: absolute; left: 67px; top: 168px;
    display: flex; align-items: center; gap: 18px;
  }
  .brand-mark { width: 44px; height: 44px; background: var(--orange); }
  .brand-name {
    font-family: "Michroma", sans-serif; font-size: 31px;
    color: var(--white); letter-spacing: 1px; white-space: nowrap;
  }

  .holder-name {
    position: absolute; left: 67px; top: 520px;
    font-family: "Michroma", sans-serif; font-size: 46px;
    color: var(--orange); letter-spacing: 2px; white-space: nowrap;
  }
  .holder-role {
    position: absolute; left: 67px; top: 585px;
    font-family: "Roboto", sans-serif; font-weight: 500; font-size: 29px;
    color: var(--white); letter-spacing: -0.5px;
  }
  .title-rule {
    position: absolute; left: 67px; top: 641px;
    width: 439px; height: 3px; background: var(--rule);
  }
  .title-rule::before {
    content: ""; position: absolute; left: 0; top: 0;
    width: 182px; height: 3px; background: var(--red);
  }
  .holder-trade {
    position: absolute; left: 69px; top: 667px;
    font-family: "Roboto", sans-serif; font-weight: 500; font-size: 28px;
    color: var(--white); letter-spacing: 1.5px; white-space: nowrap;
  }

  .contact-line {
    position: absolute; left: 78px;
    display: flex; align-items: center; gap: 22px;
  }
  .contact-line.phone { top: 821px; }
  .contact-line.email { top: 906px; }
  .contact-icon {
    width: 56px; height: 56px; background: var(--red);
    display: flex; align-items: center; justify-content: center;
  }
  .contact-text {
    font-family: "Open Sans", sans-serif; font-weight: 600;
    color: var(--grey-text); white-space: nowrap;
  }
  .phone .contact-text { font-size: 40px; letter-spacing: 1px; }
  .email .contact-text { font-size: 25px; letter-spacing: 0.5px; }
</style>
</head>
<body>
  <article class="business-card">
    <svg class="card-facets" width="648" height="1080" viewBox="0 0 648 1080" aria-hidden="true">
      <polygon points="0,0 648,0 648,90 350,260 0,140" fill="var(--facet)"/>
      <polygon points="0,140 350,260 180,330 0,400" fill="var(--facet)"/>
      <polygon points="350,260 648,90 648,380" fill="rgba(255,255,255,0.025)"/>
      <polygon points="0,400 180,330 648,540 648,620 0,440" fill="rgba(0,0,0,0.12)"/>
      <polygon points="180,330 340,250 648,380 648,540" fill="rgba(255,255,255,0.02)"/>
    </svg>

    <div class="brand">
      <span class="brand-mark"></span>
      <span class="brand-name">HALVERN ELECTRIC</span>
    </div>

    <h1 class="holder-name">NED FOSKY</h1>
    <p class="holder-role">OWNER</p>
    <div class="title-rule"></div>
    <p class="holder-trade">JOURNEYMAN ELECTRICIAN</p>

    <div class="contact-line phone">
      <span class="contact-icon">
        <svg width="34" height="30" viewBox="0 0 34 30" aria-hidden="true">
          <path d="M2 9 Q17 0 32 9 L29 14 L23 12 L22 8 Q17 6 12 8 L11 12 L5 14 Z" fill="#fff"/>
          <path d="M9 14 L25 14 L29 27 L5 27 Z" fill="#fff"/>
          <circle cx="17" cy="20" r="3.5" fill="var(--red)"/>
        </svg>
      </span>
      <span class="contact-text">1.555.208.3471</span>
    </div>

    <div class="contact-line email">
      <span class="contact-icon">
        <svg width="34" height="24" viewBox="0 0 34 24" aria-hidden="true">
          <rect x="1" y="1" width="32" height="22" fill="none" stroke="#fff" stroke-width="2"/>
          <polyline points="1,1 17,14 33,1" fill="none" stroke="#fff" stroke-width="2"/>
          <polyline points="1,23 13,11 M33,23 21,11" fill="none" stroke="#fff" stroke-width="2"/>
        </svg>
      </span>
      <span class="contact-text">kqlhalvernelectric@quellmail.net</span>
    </div>
  </article>
</body>
</html>
```